BOLD & MINIMALIST DESIGN NEEDED

We want a very bold but minimalistic business card design that is impactful and utilizes both sides of the business card. Our current logo is included for your use.

We want bold fonts and good use of negative space. We don't want the logo to overpower the design.

Target Market(s)

Professionals who are building new commercial buildings.

Industry/Entity Type

Construction

Contact Information for Business Card

Name, Title, email, office phone, cell phone, website

Font styles to use
Serif
Sans Serif

Requirements
Must have
• Bold design!

```html
<!DOCTYPE html>
<html lang="en">
<head>
<meta charset="UTF-8">
<title>Crestline – Business Card</title>
<link rel="stylesheet" href="https://fonts.googleapis.com/css2?family=Arimo:wght@400;700&display=swap">
<style>
  :root {
    --backdrop: #e4e4e4;
    --card-white: #ffffff;
    --card-dark: #2a2a2a;
    --ink: #111111;
    --ink-soft: #4a4a4a;
    --emboss: #1b1b1b;
    --accent: #8cc63f;
    --accent-light: #a6d95a;
    --rule: #c8c8c8;
  }
  * { box-sizing: border-box; margin: 0; padding: 0; }
  html, body {
    width: 1200px; height: 1200px; overflow: hidden;
    background: var(--backdrop);
    font-family: "Arimo", Arial, sans-serif;
  }
  .card {
    position: absolute;
    width: 688px; height: 393px;
  }
  .card--front { left: 267px; top: 159px; background: var(--card-white); }
  .card--back  { left: 262px; top: 653px; background: var(--card-dark); }

  /* front: brand */
  .brand {
    position: absolute; left: 50px; width: 300px; top: 170px;
    display: flex; align-items: center; justify-content: center; gap: 12px;
  }
  .brand__mark { width: 22px; height: 22px; background: var(--accent); }
  .brand__name {
    font-weight: 700; font-size: 38px; color: var(--ink); letter-spacing: 0.5px;
  }
  .divider {
    position: absolute; left: 366px; top: 90px; width: 1px; height: 154px;
    background: var(--rule);
  }

  /* front: contact */
  .contact { position: absolute; left: 390px; top: 86px; }
  .contact__name {
    font-weight: 700; font-size: 27px; color: var(--ink); letter-spacing: 0.5px;
  }
  .contact__title { font-size: 15px; color: var(--accent); margin-top: 3px; }
  .contact__list { list-style: none; margin-top: 34px; }
  .contact__item {
    display: flex; align-items: center; gap: 10px;
    font-size: 16px; color: var(--ink-soft); height: 21px;
  }
  .contact__icon { width: 14px; height: 14px; flex: none; }

  /* front: footer band */
  .band {
    position: absolute; left: 0; right: 0; top: 324px; height: 34px;
  }
  .band__web {
    position: absolute; left: 0; width: 536px; height: 100%;
    background: var(--ink); color: #fff; font-size: 16px;
    padding-left: 103px; display: flex; align-items: center;
  }
  .band__mark {
    position: absolute; left: 550px; top: 10px; width: 14px; height: 14px;
    background: var(--accent);
  }
  .band__accent {
    position: absolute; left: 580px; right: 0; height: 100%;
    background: linear-gradient(90deg, var(--accent), var(--accent-light) 50%, var(--accent));
  }

  /* back */
  .back-brand {
    position: absolute; left: 0; right: 0; top: 165px;
    display: flex; align-items: center; justify-content: center; gap: 20px;
  }
  .back-brand__mark { width: 44px; height: 44px; background: var(--emboss); }
  .back-brand__name {
    font-weight: 700; font-size: 64px; color: var(--emboss); letter-spacing: 1px;
  }
</style>
</head>
<body>

<section class="card card--front" aria-label="Business card front">
  <div class="brand">
    <span class="brand__mark"></span>
    <span class="brand__name">CRESTLINE</span>
  </div>

  <div class="divider"></div>

  <div class="contact">
    <h1 class="contact__name">DANIEL MARSH</h1>
    <p class="contact__title">President</p>
    <ul class="contact__list">
      <li class="contact__item">
        <svg class="contact__icon" viewBox="0 0 16 16"><path fill="#222" d="M3.5 1.5l2.5 0 1 3.5-1.8 1.2c.9 1.9 2.4 3.4 4.3 4.3L10.7 8.7l3.5 1v2.5c0 .9-.8 1.8-1.8 1.6C6.6 13 3 9.4 2 3.4 1.8 2.4 2.6 1.5 3.5 1.5z"/></svg>
        555-210-4871
      </li>
      <li class="contact__item">
        <svg class="contact__icon" viewBox="0 0 16 16"><rect x="4" y="1" width="8" height="14" rx="1.2" fill="none" stroke="#222" stroke-width="1.6"/><circle cx="8" cy="12.5" r="0.9" fill="#222"/></svg>
        555-392-6604
      </li>
      <li class="contact__item">
        <svg class="contact__icon" viewBox="0 0 16 16"><rect x="1" y="4" width="14" height="9" fill="#222"/><path d="M1 4l7 5 7-5" fill="none" stroke="#fff" stroke-width="1.2"/></svg>
        info@crestline.com
      </li>
    </ul>
  </div>

  <div class="band">
    <div class="band__web">www.crestline.com</div>
    <span class="band__mark"></span>
    <div class="band__accent"></div>
  </div>
</section>

<section class="card card--back" aria-label="Business card back">
  <div class="back-brand">
    <span class="back-brand__mark"></span>
    <span class="back-brand__name">CRESTLINE</span>
  </div>
</section>

</body>
</html>
```